Legal firm website redesign

Existing site for Sydney CBD lawyer needs clean and professional redesign - http://brintonlaw.com.au

The site will be viewed by a wide range of users: businesses, individuals, referral partners and other lawyers.

Please see the list of must haves for further details

Target Market(s)

Businesses, individuals, referral partners and other lawyers

Industry/Entity Type

Lawyer

Requirements
Must have
• Prominent display of phone number.
List of services down the left hand side of the site (5x services or so).
Search box in header.
Please use the greys and blues from the existing header.
New header must include the wording "Efficiency - Fulfillment - Integrity - Teamwork"

```html
<!DOCTYPE html>
<html lang="en">
<head>
<meta charset="utf-8">
<title>Brinton Law</title>
<link rel="stylesheet" href="https://fonts.googleapis.com/css2?family=Open+Sans:wght@400;600&family=Marcellus&family=Merriweather:wght@700&display=swap">
<style>
:root{
  --header-grey:#5e5e5e;
  --text:#555;
  --text-dark:#333;
  --blue:#1593c9;
  --blue-light:#3bb5e8;
  --blue-dark:#0a78b3;
  --orange:#e8620c;
  --green:#6a932e;
  --tab-grey:#a5a5a5;
  --panel:#efefef;
  --footer:#3d3d3d;
  --white:#fff;
}
*{margin:0;padding:0;box-sizing:border-box}
html,body{width:969px;height:1200px;overflow:hidden}
body{position:relative;background:var(--white);font-family:"Open Sans",Arial,sans-serif;color:var(--text)}
.abs{position:absolute}
.site-header{left:0;top:0;width:969px;height:160px;background:var(--header-grey)}
.brand{left:76px;top:48px;font-family:"Merriweather",Georgia,serif;font-weight:700;font-size:34px;color:var(--white);letter-spacing:-0.5px}
.contact-block{left:679px;top:46px;font-family:"Marcellus",Georgia,serif;color:var(--white);font-size:17px;line-height:22px;white-space:nowrap}
.contact-block b{font-weight:400;font-size:18px}
.contact-block .indent{padding-left:82px}
.service-band{left:0;top:160px;width:969px;height:303px;background:linear-gradient(#e6e6e6,#d6d6d6);border-bottom:1px solid #cfcfcf}
.main-nav{left:45px;top:137px;width:877px;height:44px;border-radius:4px 4px 0 0;background:linear-gradient(var(--blue-light),var(--blue-dark));display:flex;align-items:center;padding-left:20px}
.main-nav a{color:var(--white);font-size:12px;font-weight:600;text-decoration:none;padding:0 10px;border-right:1px solid rgba(255,255,255,.25)}
.main-nav a:last-of-type{border-right:0}
.search{position:absolute;right:14px;top:12px;width:150px;height:20px;border-radius:10px;background:var(--white);font-size:11px;font-style:italic;color:#333;padding:3px 10px}
.search svg{position:absolute;right:8px;top:5px}
.services{left:48px;top:196px;width:197px}
.services h2{font-weight:400;font-size:16px;color:var(--text-dark);margin-bottom:6px}
.services li{list-style:none;font-size:11.5px;letter-spacing:-0.2px;white-space:nowrap;color:#666;height:31.4px;line-height:31px;border-bottom:1px solid #c8c8c8;padding-left:18px;position:relative}
.services li:last-child{border-bottom:0}
.services li::before{content:"";position:absolute;left:2px;top:14px;width:11px;height:3px;background:#888;border-radius:1px}
.hero{left:256px;top:186px;width:670px;height:238px;background:linear-gradient(160deg,#e9d8b8 0%,#f5f2ec 35%,#eeeeee 70%,#d9d9d9 100%)}
.tabs{left:256px;top:424px;width:670px;height:51px;display:flex}
.tabs div{height:51px;display:flex;align-items:center;justify-content:center;font-family:"Marcellus",Georgia,serif;font-size:18px;color:var(--white);text-shadow:1px 1px 1px rgba(0,0,0,.4);border-top:2px solid rgba(255,255,255,.35)}
.t-eff{width:178px;background:var(--orange)}
.t-ful{width:178px;background:var(--blue)}
.t-int{width:166px;background:var(--green)}
.t-team{width:148px;background:var(--tab-grey)}
.dots{left:569px;top:487px;display:flex;gap:3px}
.dots span{width:13px;height:13px;border-radius:50%;background:#555;border:2px solid #ccc}
.dots .on{background:var(--blue)}
.frame{border:1px solid #d5d5d5;padding:4px;background:var(--white)}
.frame div{width:100%;height:100%}
.welcome-thumb{left:45px;top:510px;width:193px;height:128px}
.welcome{left:268px;top:504px;width:630px}
.welcome h1{font-weight:400;font-size:15.5px;color:var(--blue);margin-bottom:12px}
.welcome p{font-size:9.8px;line-height:22.3px;color:#555;letter-spacing:-0.1px}
.feature{top:672px;width:193px}
.feature h3{font-weight:400;font-size:15.5px;margin-bottom:9px;padding-left:4px}
.feature .frame{height:128px}
.feature p{font-size:9.8px;line-height:17px;text-align:justify;padding:8px 4px 0;color:#666}
.bottom-panel{left:45px;top:914px;width:882px;height:205px;background:var(--panel);border:1px solid #dcdcdc}
.panel-title{font-weight:400;font-size:15.5px;color:var(--blue)}
.additions{left:66px;top:930px}
.add-col{top:954px;font-size:9.8px;line-height:22.2px;color:#555;white-space:nowrap}
.news-divider{left:640px;top:915px;width:1px;height:203px;background:linear-gradient(#e4e4e4,#d5d5d5)}
.news{left:675px;top:930px;width:240px}
.news-item{display:flex;gap:10px;font-size:9.8px;line-height:17px;color:#555;padding:10px 0}
.news-item + .news-item{border-top:1px dashed #bbb;margin-top:6px}
.news-item em{display:block;font-size:9.5px;color:#333;font-weight:600}
.site-footer{left:0;top:1140px;width:969px;height:60px;background:var(--footer)}
.footer-links{left:51px;top:1153px;font-size:10px;line-height:17px;color:#bbb}
.connect{left:602px;top:1159px;font-size:15px;color:#aaa}
.social{left:734px;top:1156px;display:flex;gap:12px}
.social span{width:24px;height:24px;border-radius:4px}
</style>
</head>
<body>
<header class="site-header abs"></header>
<div class="brand abs">brinton law</div>
<div class="contact-block abs">
  <div><b>CALL US:</b> (02) 9431 2760</div>
  <div class="indent">(02) 9431 2785</div>
  <div><b>EMAIL</b> &nbsp;: info@brintonlaw.com.au</div>
</div>

<div class="service-band abs"></div>

<nav class="main-nav abs">
  <a href="#">Home</a><a href="#">About Us</a><a href="#">Areas of Law</a><a href="#">Publications</a><a href="#">Contact</a>
  <div class="search">Search
    <svg width="10" height="10" viewBox="0 0 10 10"><circle cx="4" cy="4" r="3" fill="none" stroke="#999" stroke-width="1.3"/><line x1="6.2" y1="6.2" x2="9.5" y2="9.5" stroke="#999" stroke-width="1.5"/></svg>
  </div>
</nav>

<aside class="services abs">
  <h2>Our Service</h2>
  <ul>
    <li>Financing</li><li>Leasing</li><li>Property transactions</li><li>Joint ventures</li>
    <li>Business restructuring</li><li>Contract review and advice</li><li>Employment Law Documentation</li>
  </ul>
</aside>

<div class="hero abs" role="img" aria-label="Close-up of a gold pen resting on a signed legal document"></div>
<div class="tabs abs">
  <div class="t-eff">EFFICIENCY</div><div class="t-ful">FULLFILLMENT</div><div class="t-int">INTEGRITY</div><div class="t-team">TEAM WORK</div>
</div>
<div class="dots abs"><span></span><span class="on"></span><span></span><span></span></div>

<div class="welcome-thumb frame abs"><div role="img" aria-label="Wooden gavel on a real property law book" style="background:linear-gradient(135deg,#1f2a3a,#6b4a2a 55%,#b07a3e)"></div></div>
<section class="welcome abs">
  <h1>Welcome To Brinton Law</h1>
  <p>Brinton Law is a dynamic commercial law firm in the CBD of Sydney providing services to corporate, small business and private clients.</p>
  <p>Brinton Law brings together over 30 years of experience in legal practice.</p>
  <p>The strong focus of the firm is on commercial law and estate planning.</p>
  <p>Brinton Law is committed to providing quality legal services in helping its clients achieve their objectives by providing a proactive understanding of its clients' businesses and creative legal solutions.</p>
</section>

<div class="feature abs" style="left:45px">
  <h3 style="color:var(--orange)">EFFICIENCY</h3>
  <div class="frame"><div role="img" aria-label="Row of small house shapes rated green to red for energy efficiency" style="background:linear-gradient(90deg,#6cbf3a,#d6d43a,#f0a030,#e2452a)"></div></div>
  <p>It is a long established fact that a reader will be distracted by the readable content .</p>
</div>
<div class="feature abs" style="left:269px">
  <h3 style="color:var(--blue)">FULLFILLMENT</h3>
  <div class="frame"><div role="img" aria-label="Illustration of rising growth bars with an upward arrow" style="background:linear-gradient(90deg,#ffffff 0%,#dfeaf4 40%,#f4f4f6 100%)"></div></div>
  <p>It is a long established fact that a reader will be distracted by the readable content .</p>
</div>
<div class="feature abs" style="left:501px">
  <h3 style="color:var(--green)">INTEGRITY</h3>
  <div class="frame"><div role="img" aria-label="Two business people shaking hands" style="background:linear-gradient(90deg,#3a3f48,#c9a08a 50%,#2e3238)"></div></div>
  <p>It is a long established fact that a reader will be distracted by the readable content .</p>
</div>
<div class="feature abs" style="left:715px">
  <h3 style="color:#888">TEAM WORK</h3>
  <div class="frame"><div role="img" aria-label="Team members stacking hands together" style="background:radial-gradient(circle at 50% 50%,#c79a80,#2b2b2b 70%)"></div></div>
  <p>It is a long established fact that a reader will be distracted by the readable content .</p>
</div>

<section class="bottom-panel abs"></section>
<h2 class="panel-title additions abs">Recent Additions</h2>
<div class="add-col abs" style="left:66px">
  Commencement of the Succession Act 2006 25.03.08<br>Is that will valid? 15.01.08<br>Labor's proposed changes to IR laws 14.12.07<br>Should you make your own will? 14.11.07<br>Illegal workers 14.08.07<br>Employees' liability for misleading or deceptive conduct<br>14.08.07
</div>
<div class="add-col abs" style="left:344px">
  Correct use of ACNs and ABNs 14.08.07<br>Power of Attorney Infosheet 10.08.07<br>Intestate Estates Infosheet 08.08.07<br>Estate Planning Infosheet 07.06.07<br>Special Disability Trusts Infosheet 18.05.07<br>Testamentary Trusts Infosheet 17.05.07<br>Appointment of an Enduring Guardian Infosheet 15.05.07
</div>
<div class="news-divider abs"></div>
<section class="news abs">
  <h2 class="panel-title">Latest News</h2>
  <div class="news-item">
    <svg width="24" height="24" viewBox="0 0 24 24"><rect x="2" y="4" width="20" height="18" fill="#f4f4f4" stroke="#aaa"/><rect x="2" y="4" width="20" height="4" fill="#bbb"/><text x="12" y="19" font-size="9" text-anchor="middle" fill="#999" font-family="Open Sans,sans-serif">27</text></svg>
    <div>It is a long established fact that a reader will be distracted by the readable content .<em>Mar 9, 2012</em></div>
  </div>
  <div class="news-item">
    <svg width="24" height="24" viewBox="0 0 24 24"><rect x="2" y="4" width="20" height="18" fill="#f4f4f4" stroke="#aaa"/><rect x="2" y="4" width="20" height="4" fill="#bbb"/><text x="12" y="19" font-size="9" text-anchor="middle" fill="#999" font-family="Open Sans,sans-serif">27</text></svg>
    <div>It is a long established fact that a reader will be distracted by the readable content .<em>Mar 9, 2012</em></div>
  </div>
</section>

<footer class="site-footer abs"></footer>
<div class="footer-links abs">Home | About Us | Area of Law | Our People | Publication | Contact<br>Copyright@2012 &nbsp;www.brintonlaw.com.au</div>
<div class="connect abs">Connect With Us</div>
<div class="social abs"><span style="background:#3b5a9a"></span><span style="background:#4cb6e0"></span><span style="background:#e8762a"></span><span style="background:#1f7bb6"></span><span style="background:#356aa0"></span></div>
</body>
</html>
```